Seed Oil Safety Card for Healthy Restaurant Dining

I am seeking a design for a physical card to communicate my wife's health-related dietary restriction regarding seed oils. This card will be given to restaurant waiters to ensure her meals are prepared without seed oils, as it is a health issue and not merely a preference.
My wife cannot eat any “seed oil” or “processed oil”, including:
- Vegetable oil
- Canola oil
- Soybean oil
- Sunflower oil
- Corn oil
- Cottonseed oil
- Safflower oil
- Peanut oil
- Sesame oil
Oils that are OK for her to consume:
- Butter (most preferable)
- Extra virgin olive oil
- Avocado oil
- Coconut oil
- Ghee
- Lard
- Any other animal-based fats
Key Design Requirements:
- Clarity and speed of communication: The card should be easily read and understood by waiters, even in low-light environments, emphasizing that it's a health concern.
- Avoid common misconceptions: Ensure the design doesn't imply common dietary preferences like "vegetarian" or "no butter." Animal fats and butter are actually preferable for her!
- Preferred term: Use "seed oils" as the term to describe what she cannot eat due to her health issue.
- Trace amounts are acceptable: Communicate that it's OK to use cookware that has previously been in contact with seed oils, but not to have seed oil as an ingredient. Please suggest a concise way to convey this.
- Card dimensions: Design should be 3.5” x 2.25” (standard credit-card size on printorvale.example). Horizontal or vertical layouts are both fine, whichever makes the message clearer.
Design Suggestions:
- Utilize bold and easy-to-read typography to communicate the main message.
- Consider incorporating relevant icons or graphics that help convey the message without adding confusion.
- Use contrasting colors to enhance readability, especially in low-light situations.
- To communicate the “trace amounts OK” part, consider phrases such as:
- "Cross-contamination acceptable"
- “Used cookware OK, no ingredient use”
- “Separate cookware not necessary”
Thank you for your assistance in creating this essential card for my wife's health and safety when dining out!

```html
<!DOCTYPE html>
<html lang="en">
<head>
<meta charset="utf-8">
<title>Food Restriction Card</title>
<link rel="stylesheet" href="https://fonts.googleapis.com/css2?family=Oswald:wght@700&family=Open+Sans:wght@600;700;800&display=swap">
<style>
  :root {
    --red: #cc0000;
    --title-red: #ee0a0a;
    --green: #00b300;
    --green-text: #009900;
    --ink: #1c1c1c;
    --band: #1e1e1e;
    --amber: #f5a623;
    --white: #ffffff;
    --page: #ffffff;
    --edge: #d6d6d6;
  }
  * { box-sizing: border-box; margin: 0; padding: 0; }
  html, body { width: 849px; height: 1200px; overflow: hidden; background: var(--page); }
  .sheet { position: relative; width: 849px; height: 1200px; }
  .card {
    position: absolute; top: 483px; width: 363px; height: 234px;
    border-radius: 12px; overflow: hidden;
    box-shadow: 0 0 0 1px var(--edge), 0 2px 4px rgba(0,0,0,0.12);
  }
  .card--front { left: 52px; background: var(--white); }
  .card--back { left: 434px; }

  .card__title {
    position: absolute; left: 0; right: 0; top: 12px; text-align: center;
    font-family: "Oswald", "Arial Narrow", sans-serif; font-weight: 700;
    font-size: 31px; line-height: 1; color: var(--title-red); letter-spacing: 0.3px;
  }
  .panel {
    position: absolute; top: 53px; width: 157px; height: 139px;
    clip-path: polygon(0 0, 100% 0, 100% 88%, 88% 100%, 0 100%);
    font-family: "Open Sans", Arial, sans-serif; color: var(--white);
  }
  .panel--banned { left: 21px; background: var(--red); }
  .panel--allowed { left: 187px; background: var(--green); }
  .panel__icon { position: absolute; left: 4px; top: 6px; width: 20px; height: 14px; }
  .panel__head {
    position: absolute; left: 27px; right: 2px; top: 2px; height: 25px;
    background: var(--white); text-align: center;
  }
  .panel__name { font-weight: 700; font-size: 11.5px; line-height: 13px; color: #333; display: block; margin-top: 1px; }
  .panel__status { font-weight: 800; font-size: 7.5px; line-height: 9px; display: block; }
  .panel--banned .panel__status { color: var(--red); }
  .panel--allowed .panel__status { color: var(--green-text); }
  .panel__list {
    list-style: none; position: absolute; left: 0; right: 0; text-align: center;
    font-weight: 800; font-size: 8.6px; line-height: 10.6px; letter-spacing: 0.6px;
  }
  .panel--banned .panel__list { top: 36px; }
  .panel--allowed .panel__list { top: 46px; }
  .panel__list li::before { content: "· "; }
  .panel__note { font-size: 5.5px; font-weight: 700; letter-spacing: 0.2px; }

  .card__band {
    position: absolute; left: 0; right: 0; bottom: 0; height: 33px; background: var(--band);
    display: flex; align-items: center; justify-content: center; gap: 8px;
    font-family: "Open Sans", Arial, sans-serif; font-weight: 700; font-size: 9px;
    color: var(--amber); letter-spacing: 0.3px;
  }
  .card__band svg { width: 15px; height: 13px; }

  .card__photo {
    position: absolute; inset: 0;
    background: linear-gradient(135deg, #e8e6e0 0%, #e9b93a 30%, #f1f0ea 52%, #e6c04a 72%, #ecebe6 100%);
  }
  .card__ribbon {
    position: absolute; left: 0; right: 0; top: 92px; height: 50px;
    background: rgba(255,255,255,0.72);
    display: flex; align-items: center; justify-content: center;
  }
  .card__ribbon .card__title { position: static; font-size: 32px; }
</style>
</head>
<body>
<main class="sheet">
  <section class="card card--front">
    <h1 class="card__title">FOOD RESTRICTION CARD</h1>

    <div class="panel panel--banned">
      <svg class="panel__icon" viewBox="0 0 20 14" aria-hidden="true">
        <circle cx="5" cy="6" r="4" fill="none" stroke="#fff" stroke-width="1"/>
        <path d="M3.2 4.2l3.6 3.6M6.8 4.2l-3.6 3.6" stroke="#fff" stroke-width="1"/>
        <path d="M11 2h6v5h-2l-1 5h-1.5V7H11z" fill="#fff"/>
      </svg>
      <div class="panel__head">
        <span class="panel__name">Processed Oil</span>
        <span class="panel__status">Not Allowed</span>
      </div>
      <ul class="panel__list">
        <li>Corn oil</li>
        <li>Canola oil</li>
        <li>Peanut oil</li>
        <li>Sesame oil</li>
        <li>Soybean oil</li>
        <li>Safflower oil</li>
        <li>Sunflower oil</li>
        <li>Vegetable oil</li>
        <li>Cottonseed oil</li>
      </ul>
    </div>

    <div class="panel panel--allowed">
      <svg class="panel__icon" viewBox="0 0 20 14" aria-hidden="true">
        <circle cx="5" cy="8" r="4" fill="none" stroke="#fff" stroke-width="1"/>
        <path d="M3 8l1.5 1.5L7 6.5" fill="none" stroke="#fff" stroke-width="1"/>
        <path d="M11 12h6V7h-2l-1-5h-1.5v5H11z" fill="#fff"/>
      </svg>
      <div class="panel__head">
        <span class="panel__name">Natural Oil</span>
        <span class="panel__status">Allowed</span>
      </div>
      <ul class="panel__list">
        <li>Butter <span class="panel__note">(most preferable)</span></li>
        <li>Extra virgin olive oil</li>
        <li>Animal-based fats</li>
        <li>Avocado oil</li>
        <li>Coconut oil</li>
        <li>Lard</li>
        <li>Ghee</li>
      </ul>
    </div>

    <footer class="card__band">
      <svg viewBox="0 0 15 13" aria-hidden="true">
        <path d="M7.5 1L14 12H1z" fill="none" stroke="var(--amber)" stroke-width="1"/>
        <path d="M7.5 5v3.5" stroke="var(--amber)" stroke-width="1.2"/>
        <circle cx="7.5" cy="10" r="0.7" fill="var(--amber)"/>
      </svg>
      <span>Cross-contamination acceptable</span>
    </footer>
  </section>

  <section class="card card--back">
    <div class="card__photo" role="img" aria-label="Photo of plastic bottles of golden cooking oil lying on a light grey surface"></div>
    <div class="card__ribbon">
      <h2 class="card__title">FOOD RESTRICTION CARD</h2>
    </div>
  </section>
</main>
</body>
</html>
```